New Bicycle shop business card

Hi!
I'm looking for a business card for my new proffesional bike mechanics shop. This shop is only for fixing broken bikes and not selling bikes.
Peferbly a modern and sleek and modern design.
Colors: black, grey, red, white
Information:
Name: Rijwielwerkplaats Vanhoutte
Shop owner: Bart Vanhoutte & Marieke Segers
Website: www.rijwielwerkplaats-vanhoutte.be
Email: info@rijwielwerkplaats-vanhoutte.be
Phone number: +32471902368
Street adres: Kerkweg 46
9940 Bellebeke
Slogan/shop information: Herstellingen van alle merken.
Logo: see files.
Target Market(s)
People who seek a mechanic to fix or upgrade their bikes.
Contact Information for Business Card
Information:
Website: info@rijwielwerkplaats-vanhoutte.be
9940 Bellebeke
Logo: see files.

```html
<!DOCTYPE html>
<html lang="nl">
<head>
<meta charset="utf-8">
<title>Rijwielwerkplaats Vanhoutte – visitekaartje</title>
<link href="https://fonts.googleapis.com/css2?family=Montserrat:wght@700;800&family=Roboto:wght@400;500&display=swap" rel="stylesheet">
<style>
  :root {
    --bg: #3a3a3c;
    --card-black: #1c1c1e;
    --red: #e0313f;
    --grey: #9a9b9f;
    --white: #ffffff;
    --white-soft: #f4f4f4;
    --gloss: #5a5a5e;
  }
  * { margin: 0; padding: 0; box-sizing: border-box; }
  html, body { width: 799px; height: 1200px; overflow: hidden; }
  body {
    background: var(--bg);
    display: flex;
    flex-direction: column;
    align-items: center;
    justify-content: center;
    gap: 120px;
    font-family: "Roboto", Arial, sans-serif;
  }
  .card {
    position: relative;
    width: 580px;
    height: 330px;
    border-radius: 22px;
    overflow: hidden;
    box-shadow: 0 14px 30px rgba(0,0,0,.45);
  }
  /* front */
  .card--front {
    background: var(--card-black);
    display: flex;
    align-items: center;
    justify-content: center;
    gap: 14px;
  }
  .front-mark {
    width: 18px; height: 18px;
    border-radius: 50%;
    background: var(--gloss);
  }
  .front-name {
    font-family: "Montserrat", Arial, sans-serif;
    font-weight: 800;
    font-size: 26px;
    letter-spacing: 1px;
    text-transform: uppercase;
    color: var(--gloss);
  }
  /* back */
  .card--back { background: var(--red); }
  .back-shape { position: absolute; inset: 0; }
  .brand {
    position: absolute;
    left: 18px;
    top: 100px;
    width: 206px;
    text-align: center;
  }
  .brand-mark {
    display: block;
    width: 26px; height: 26px;
    margin: 0 auto 12px;
    border-radius: 50%;
    background: var(--red);
  }
  .brand-name {
    font-family: "Montserrat", Arial, sans-serif;
    font-weight: 800;
    font-size: 15px;
    line-height: 1.25;
    letter-spacing: .5px;
    text-transform: uppercase;
    color: var(--white);
  }
  .brand-slogan {
    margin-top: 10px;
    font-size: 12px;
    color: var(--white-soft);
  }
  .contact {
    position: absolute;
    left: 314px;
    top: 92px;
    color: var(--white);
  }
  .person-name {
    font-family: "Montserrat", Arial, sans-serif;
    font-weight: 700;
    font-size: 20px;
    letter-spacing: 1px;
    text-transform: uppercase;
  }
  .person-role { font-size: 13px; margin-bottom: 18px; opacity: .95; }
  .contact-list { list-style: none; font-size: 14px; line-height: 22px; }
  .contact-list li { display: flex; align-items: center; gap: 10px; }
  .contact-list svg { width: 13px; height: 13px; flex: none; fill: var(--white); }
  .address { font-size: 14px; line-height: 20px; margin-top: 6px; }
</style>
</head>
<body>

  <section class="card card--front" aria-label="Voorkant visitekaartje">
    <span class="front-mark"></span>
    <span class="front-name">Rijwielwerkplaats Vanhoutte</span>
  </section>

  <section class="card card--back" aria-label="Achterkant visitekaartje">
    <svg class="back-shape" viewBox="0 0 580 330" preserveAspectRatio="none" aria-hidden="true">
      <path d="M0 0 H302 C266 90 246 200 172 330 H0 Z" fill="var(--grey)"/>
      <path d="M0 0 H288 C252 90 230 200 152 330 H0 Z" fill="var(--card-black)"/>
    </svg>

    <div class="brand">
      <span class="brand-mark"></span>
      <p class="brand-name">Rijwielwerkplaats<br>Vanhoutte</p>
      <p class="brand-slogan">Herstellingen van alle merken</p>
    </div>

    <div class="contact">
      <p class="person-name">Marieke Segers</p>
      <p class="person-role">Owner</p>
      <ul class="contact-list">
        <li>
          <svg viewBox="0 0 24 24"><path d="M6.6 10.8a15.1 15.1 0 0 0 6.6 6.6l2.2-2.2a1 1 0 0 1 1-.25 11.4 11.4 0 0 0 3.6.57 1 1 0 0 1 1 1V20a1 1 0 0 1-1 1A17 17 0 0 1 3 4a1 1 0 0 1 1-1h3.5a1 1 0 0 1 1 1c0 1.25.2 2.45.57 3.57a1 1 0 0 1-.25 1z"/></svg>
          +32471902368
        </li>
        <li>
          <svg viewBox="0 0 24 24"><path d="M2 5h20v14H2z M2 5l10 8 10-8" fill="none" stroke="#fff" stroke-width="2"/></svg>
          www.rijwielwerkplaats-vanhoutte.be
        </li>
        <li>
          <svg viewBox="0 0 24 24"><circle cx="12" cy="12" r="9" fill="none" stroke="#fff" stroke-width="2"/><path d="M3 12h18M12 3c3 3 3 15 0 18M12 3c-3 3-3 15 0 18" fill="none" stroke="#fff" stroke-width="1.6"/></svg>
          info@rijwielwerkplaats-vanhoutte.be
        </li>
      </ul>
      <p class="address">Kerkweg 46<br>9940 Bellebeke</p>
    </div>
  </section>

</body>
</html>
```